Modern Business Card For A Digital Advertising Company

I'll be print on the Pell Prints Velour paper http://us.pellprints.com/products/velour/business-cards.html
Need's to be modern and use the color palette of the logo or gray scales. I think integrating the pixelation of the logo in to the card and having it wrap from one side to the other could be interesting. My company provides ad operations, web development, and number of other services to websites around the world. You can see my website at http://www.zantorhq.com
Contact info on the card needs to have
Owen Lasko
President
p.318.204.6637
owen@zantorhq.com
http://www.zantorhq.com
Doesn't necessarily need to be in that order
Website owners
Business

```html
<!DOCTYPE html>
<html lang="en">
<head>
<meta charset="utf-8">
<title>Zantor HQ — Business Card</title>
<link href="https://fonts.googleapis.com/css2?family=Open+Sans:wght@400;600;700;800&display=swap" rel="stylesheet">
<style>
  :root {
    --backdrop: #1f1f1f;
    --green-dark: #5f9630;
    --green: #7ab83a;
    --green-light: #8dc63f;
    --charcoal: #3b3b3b;
    --white: #ffffff;
  }
  * { margin: 0; padding: 0; box-sizing: border-box; }
  html, body {
    width: 1200px; height: 757px; overflow: hidden;
    background: var(--backdrop);
    font-family: "Open Sans", sans-serif;
  }
  .stage { position: relative; width: 1200px; height: 757px; }

  .card {
    position: absolute; width: 560px; height: 330px;
    border-radius: 22px; overflow: hidden;
  }
  .card-front { left: 40px; top: 70px; background: var(--white); }
  .card-back {
    left: 610px; top: 360px;
    background: linear-gradient(135deg, var(--green-dark) 0%, var(--green) 55%, var(--green-light) 100%);
  }
  .card-art { position: absolute; inset: 0; width: 100%; height: 100%; }

  .brand {
    position: absolute; display: flex; align-items: center; gap: 12px;
    color: var(--green); font-weight: 800; letter-spacing: 1px;
  }
  .card-front .brand { left: 190px; top: 62px; font-size: 30px; }
  .brand-square { width: 26px; height: 26px; background: currentColor; }
  .card-back .brand { left: 0; right: 0; top: 100px; justify-content: center; color: var(--white); font-size: 58px; gap: 20px; }
  .card-back .brand-square { width: 48px; height: 48px; }

  .identity {
    position: absolute; right: 232px; top: 240px; text-align: right; color: var(--white);
  }
  .identity-name { font-size: 20px; font-weight: 700; line-height: 1.1; }
  .identity-role { font-size: 12px; font-weight: 400; }

  .divider {
    position: absolute; left: 340px; top: 232px; width: 1px; height: 62px;
    background: rgba(255,255,255,0.6);
  }

  .contact {
    position: absolute; left: 354px; top: 232px; list-style: none;
    color: var(--white); font-size: 12.5px; line-height: 20px;
  }
  .contact li { display: flex; align-items: center; gap: 7px; }
  .contact svg { width: 11px; height: 11px; fill: var(--white); flex: none; }

  .back-url {
    position: absolute; left: 0; right: 0; bottom: 52px; text-align: center;
    color: var(--white); font-size: 19px; font-weight: 700; letter-spacing: 1px;
  }
</style>
</head>
<body>
<main class="stage">

  <section class="card card-front" aria-label="Business card front">
    <svg class="card-art" viewBox="0 0 560 330" preserveAspectRatio="none" aria-hidden="true">
      <defs>
        <linearGradient id="frontGreen" x1="0" y1="1" x2="1" y2="0">
          <stop offset="0" stop-color="#5f9630"/>
          <stop offset="1" stop-color="#8dc63f"/>
        </linearGradient>
      </defs>
      <path d="M0 196 Q300 226 560 112 L560 330 L0 330 Z" fill="url(#frontGreen)"/>
      <path d="M0 172 Q300 214 470 126 Q310 200 0 188 Z" fill="#3b3b3b"/>
    </svg>

    <div class="brand"><span class="brand-square"></span>ZANTOR HQ</div>

    <div class="identity">
      <div class="identity-name">Owen Lasko</div>
      <div class="identity-role">President</div>
    </div>
    <div class="divider"></div>
    <ul class="contact">
      <li><svg viewBox="0 0 12 12"><path d="M2.5 1 L4.5 1 L5.3 3.6 L4 4.6 Q5 7 7.4 8 L8.4 6.7 L11 7.5 L11 9.5 Q11 11 9.5 11 Q1 10 1 2.5 Q1 1 2.5 1 Z"/></svg>318.204.6637</li>
      <li><svg viewBox="0 0 12 12"><path d="M1 2.5 H11 V9.5 H1 Z M1.6 3 L6 6.6 L10.4 3 Z" fill-rule="evenodd"/></svg>owen@zantorhq.com</li>
      <li><svg viewBox="0 0 12 12"><circle cx="6" cy="6" r="5"/><path d="M1 6 H11 M6 1 Q3 6 6 11 Q9 6 6 1" stroke="#6fa838" stroke-width="0.9" fill="none"/></svg>www.zantorhq.com</li>
    </ul>
  </section>

  <section class="card card-back" aria-label="Business card back">
    <div class="brand"><span class="brand-square"></span>ZANTOR HQ</div>
    <div class="back-url">www.zantorhq.com</div>
  </section>

</main>
</body>
</html>
```